BUSINESS CARD DESIGN

NAME- DALE VORSKIN
PHONE NUMER - 555- 714-9082
EMAIL- OFFICE@TRV-GROUNDMAKRZ.COM
BACK OF CARD- SPEACIALIZES IN LAND CLEARING, FORESTRY MUCLHING AND EXCAVATION

Contact Information for Business Card

NAME- DALE VORSKIN PHONE NUMER - 555- 714-9082 EMAIL- OFFICE@TRV-GROUNDMAKRZ.COM BACK OF CARD- SPEACIALIZES IN LAND CLEARING , MUCLHING AND EXCAVATION

```html
<!DOCTYPE html>
<html lang="en">
<head>
<meta charset="utf-8">
<title>Traverse Groundmakrz LLC — Business Card</title>
<link href="https://fonts.googleapis.com/css2?family=Roboto:wght@400&family=Ubuntu:wght@300;400;700&display=swap" rel="stylesheet">
<style>
  :root {
    --page: #e3e8ea;
    --card: #202024;
    --pattern: #1c1c1f;
    --gold: #f5b21b;
    --white: #f2f2f2;
  }
  * { margin: 0; padding: 0; box-sizing: border-box; }
  html, body { width: 1200px; height: 960px; overflow: hidden; background: var(--page); }
  .canvas { position: relative; width: 1200px; height: 960px; }

  .card {
    position: absolute; left: 250px; width: 701px; height: 400px;
    background: var(--card); border-bottom: 2px solid var(--gold); overflow: hidden;
  }
  .card-front { top: 60px; }
  .card-back { top: 500px; }

  .front-texture {
    position: absolute; inset: 0;
    background: radial-gradient(ellipse at 50% 45%, #262629 0%, var(--pattern) 80%);
  }

  .brand {
    position: absolute; left: 0; right: 0; top: 110px;
    display: flex; flex-direction: column; align-items: center; gap: 18px;
  }
  .brand-dot { width: 96px; height: 96px; border-radius: 50%; background: var(--gold); }
  .brand-name {
    font-family: "Ubuntu", sans-serif; font-weight: 700; font-size: 21px;
    letter-spacing: 2px; color: var(--gold);
  }

  .tagline {
    position: absolute; left: 0; right: 0; top: 357px; text-align: center;
    font-family: "Roboto", sans-serif; font-size: 16.5px; color: var(--gold);
    letter-spacing: 0.2px;
  }

  .holder {
    position: absolute; left: 50px; top: 176px;
    font-family: "Ubuntu", sans-serif; font-size: 40px; letter-spacing: 1px;
  }
  .holder-first { font-weight: 700; color: var(--gold); }
  .holder-last { font-weight: 300; color: var(--white); }

  .divider {
    position: absolute; left: 350px; top: 133px; width: 2px; height: 134px;
    background: var(--gold);
  }

  .contacts {
    position: absolute; left: 393px; top: 172px; list-style: none;
    font-family: "Roboto", sans-serif; font-size: 15.5px; color: var(--white);
    letter-spacing: 1px;
  }
  .contacts li { display: flex; align-items: center; gap: 11px; height: 30px; }
  .contacts svg { width: 17px; height: 17px; flex: none; }

  .website {
    position: absolute; left: 0; right: 0; top: 353px; text-align: center;
    font-family: "Roboto", sans-serif; font-size: 15.5px; color: var(--gold);
    letter-spacing: 0.8px;
  }
</style>
</head>
<body>
<div class="canvas">

  <section class="card card-front">
    <div class="front-texture" role="img" aria-label="Repeating embossed pattern of the company emblem on dark card stock"></div>
    <div class="brand">
      <span class="brand-dot"></span>
      <span class="brand-name">TRAVERSE GROUNDMAKRZ LLC</span>
    </div>
    <p class="tagline">SPEACIALIZES IN LAND CLEARING , MUCLHING AND EXCAVATION</p>
  </section>

  <section class="card card-back">
    <h1 class="holder"><span class="holder-first">DALE</span> <span class="holder-last">VORSKIN</span></h1>
    <span class="divider"></span>
    <ul class="contacts">
      <li>
        <svg viewBox="0 0 24 24" aria-hidden="true"><path fill="#f5b21b" d="M6.6 10.8a15.1 15.1 0 0 0 6.6 6.6l2.2-2.2c.3-.3.7-.4 1-.2 1.1.4 2.3.6 3.6.6.6 0 1 .4 1 1V20c0 .6-.4 1-1 1A17 17 0 0 1 3 4c0-.6.4-1 1-1h3.5c.6 0 1 .4 1 1 0 1.3.2 2.5.6 3.6.1.3 0 .7-.2 1l-2.3 2.2z"/></svg>
        <span>555- 714-9082</span>
      </li>
      <li>
        <svg viewBox="0 0 24 24" aria-hidden="true"><path fill="#f5b21b" d="M2 9l10-6 10 6v12H2z"/><path fill="none" stroke="#202024" stroke-width="1.5" d="M2 9l10 7 10-7M2 21l7-6M22 21l-7-6"/></svg>
        <span>OFFICE@TRV-GROUNDMAKRZ.COM</span>
      </li>
    </ul>
    <p class="website">WWW.TRV-GROUNDMAKRZ.COM</p>
  </section>

</div>
</body>
</html>
```